KORV PTY LTD - Business Cards

Design a modern business card - using the attached Designs.
Same design as on the front, apart from the names/numbers/emails to be different.
We want the cards to be very glossy to stand out, do I think the simple black/white/metallic will be effective.
Both lots of details below:

Tom Wrenshaw
Director
tom_korv@nulvane.com
0438 274 093

Lewis Corbyn
Director
lewis_korv@nulvane.com
0419 385 642

Industry/Entity Type

Business

```html
<!DOCTYPE html>
<html lang="en">
<head>
<meta charset="utf-8">
<title>KORV PTY LTD – Business Cards</title>
<link rel="stylesheet" href="https://fonts.googleapis.com/css2?family=Noto+Serif:wght@400&display=swap">
<style>
  :root {
    --page-bg: #e9e7e4;
    --card-dark-top: #3a3b3d;
    --card-dark-mid: #4b4c4f;
    --card-dark-bottom: #1c1d1f;
    --card-light: #b4b4b4;
    --text-light: #f1f1f1;
    --text-dark: #2a2b2d;
    --mark-light: #9c9ea1;
    --mark-dark: #2f3032;
    --shadow: rgba(0, 0, 0, 0.28);
  }
  * { box-sizing: border-box; margin: 0; padding: 0; }
  html, body {
    width: 1200px;
    height: 471px;
    overflow: hidden;
    background: var(--page-bg);
    font-family: "Noto Serif", Georgia, serif;
  }
  .canvas {
    position: relative;
    width: 1200px;
    height: 471px;
  }
  .card {
    position: absolute;
    top: 70px;
    width: 545px;
    height: 330px;
    box-shadow: 0 6px 18px var(--shadow);
  }
  .card--front { left: 30px; }
  .card--back { left: 625px; background: var(--card-light); }

  .card__texture {
    position: absolute;
    inset: 0;
    background: radial-gradient(ellipse at 55% 45%, var(--card-dark-mid) 0%, var(--card-dark-top) 45%, var(--card-dark-bottom) 100%);
  }

  .brand {
    position: absolute;
    display: flex;
    align-items: center;
    gap: 12px;
    white-space: nowrap;
  }
  .brand__dot {
    border-radius: 50%;
    flex: none;
  }
  .brand__name {
    font-weight: 400;
    letter-spacing: 0.04em;
  }
  .card--front .brand { left: 48px; top: 148px; }
  .card--front .brand__dot { width: 30px; height: 30px; background: var(--mark-light); }
  .card--front .brand__name { font-size: 22px; color: var(--text-light); }

  .card--back .brand { left: 50%; top: 50%; transform: translate(-50%, -50%); gap: 18px; }
  .card--back .brand__dot { width: 52px; height: 52px; background: var(--mark-dark); }
  .card--back .brand__name { font-size: 40px; color: var(--text-dark); }

  .contact {
    position: absolute;
    left: 296px;
    top: 92px;
    color: var(--text-light);
  }
  .contact__name { font-size: 19px; line-height: 1.2; }
  .contact__role { font-size: 13px; margin-top: 6px; }
  .contact__list { list-style: none; margin-top: 34px; font-size: 14px; }
  .contact__item { display: flex; align-items: center; gap: 7px; line-height: 1.7; }
  .contact__icon { width: 12px; height: 12px; fill: var(--text-light); flex: none; }
</style>
</head>
<body>
<main class="canvas">
  <section class="card card--front" aria-label="Business card front">
    <div class="card__texture" role="img" aria-label="Dark perforated metal texture"></div>
    <div class="brand">
      <span class="brand__dot"></span>
      <span class="brand__name">KORV PTY LTD</span>
    </div>
    <div class="contact">
      <p class="contact__name">Lewis Corbyn</p>
      <p class="contact__role">Director</p>
      <ul class="contact__list">
        <li class="contact__item">
          <svg class="contact__icon" viewBox="0 0 24 24" aria-hidden="true"><path d="M6.6 10.8a15.1 15.1 0 0 0 6.6 6.6l2.2-2.2a1 1 0 0 1 1-.25 11.4 11.4 0 0 0 3.6.57 1 1 0 0 1 1 1V20a1 1 0 0 1-1 1A17 17 0 0 1 3 4a1 1 0 0 1 1-1h3.5a1 1 0 0 1 1 1c0 1.25.2 2.45.57 3.57a1 1 0 0 1-.25 1z"/></svg>
          <span>0419 385 642</span>
        </li>
        <li class="contact__item">
          <svg class="contact__icon" viewBox="0 0 24 24" aria-hidden="true"><path d="M3 5h18a1 1 0 0 1 1 1v12a1 1 0 0 1-1 1H3a1 1 0 0 1-1-1V6a1 1 0 0 1 1-1zm1 2.2V17h16V7.2l-8 5.3z"/></svg>
          <span>lewis_korv@nulvane.com</span>
        </li>
      </ul>
    </div>
  </section>

  <section class="card card--back" aria-label="Business card back">
    <div class="brand">
      <span class="brand__dot"></span>
      <span class="brand__name">KORV PTY LTD</span>
    </div>
  </section>
</main>
</body>
</html>
```